Audio/ Video Packaging Design for a Technology company.

We need a packaging design for a bag that is 7" wide and 10" high. The design will be for a new line of audio/video products. We would like to see designs that represent a superior quality product that provides a pure connection. We want the equivalent of a nice retail bag that you would find in a store like Tallow Mart. It should be a maximum of three colors. We really want something sharp, professional and eye catching, not whimsical or cartoonish. I've included a couple of examples below. I don't really like the designs of the bags, but I want you to see examples of what I'm looking for.

The company logo, which is uploaded, should be on the design. The words "audio and video products" should be either underneath the logo or to the side. Also, somewhere on the bag, we would like the words "For a Pure Connection"

The winner of this contest will likely get the opportunity for additional work as we have more products ready to launch.

Target Market(s)

resellers, consumers - men 25-60

Industry/Entity Type

It Company

Requirements
Must have
• It should be a maximum of three colors. We really want something sharp, professional and eye catching, not whimsical or cartoonish
Nice to have
• Eye-catching design. Utilize the entire bag but don't make it too busy.
Should not have
• Whimsical, cartoonish

```html
<!DOCTYPE html>
<html lang="en">
<head>
<meta charset="utf-8">
<title>Veralink Audio and Video Products – Retail Bag</title>
<link rel="stylesheet" href="https://fonts.googleapis.com/css2?family=Questrial&family=Barlow+Condensed:wght@600&display=swap">
<style>
  :root {
    --bg: #6f9e3c;
    --frame: #7aae3a;
    --frame-dark: #5f9233;
    --lime: #b9d935;
    --leaf: #6fa63a;
    --paper: #ffffff;
    --ink: #1c1c1c;
    --seal: #e6e6e6;
  }
  * { box-sizing: border-box; margin: 0; padding: 0; }
  html, body { width: 1200px; height: 787px; overflow: hidden; }
  body {
    position: relative;
    background: var(--bg);
    font-family: "Questrial", sans-serif;
  }
  .bag {
    position: absolute;
    top: 116px;
    width: 430px;
    height: 614px;
    border-radius: 24px;
    background: linear-gradient(180deg, var(--frame), var(--frame-dark));
  }
  .bag--front { left: 152px; }
  .bag--back { left: 618px; width: 428px; }

  .bag__panel {
    position: absolute;
    left: 21px; top: 22px; right: 21px;
    border-radius: 18px 18px 0 0;
    background: var(--paper);
    height: 542px;
    overflow: hidden;
  }
  .bag__seal {
    position: absolute; left: 0; right: 0; top: 66px; height: 12px;
    border-top: 2px solid var(--seal);
    border-bottom: 2px solid var(--seal);
  }
  .bag__tab { position: absolute; left: 0; top: 0; }
  .hang-hole { position: absolute; }

  .brand-name {
    position: absolute; left: 0; right: 0;
    text-align: center;
    letter-spacing: 3px;
    line-height: 1;
  }
  .tagline {
    position: absolute; left: 0; right: 0;
    text-align: center;
    font-size: 20px;
    color: var(--ink);
  }
  .bag--front .brand-name { top: 228px; font-size: 42px; color: var(--leaf); }
  .bag--front .tagline { top: 274px; }

  .splash {
    position: absolute;
    border-radius: 50%;
    background: radial-gradient(ellipse at center, rgba(185,217,53,.9), rgba(111,166,58,.6) 45%, rgba(111,166,58,0) 72%);
  }
  .bag--front .splash { left: 250px; top: 430px; width: 200px; height: 120px; }

  .slogan-band {
    position: absolute; left: 14px; right: 14px; top: 564px; height: 40px;
    background: linear-gradient(90deg, var(--leaf), var(--lime) 50%, var(--leaf));
    display: flex; align-items: center; justify-content: center;
    font-family: "Barlow Condensed", sans-serif;
    font-weight: 600;
    font-size: 28px;
    color: var(--ink);
  }

  .bag--back .bag__panel {
    height: 572px;
    border-radius: 18px;
    background: radial-gradient(ellipse 60% 55% at 50% 62%, var(--lime), #8cbd37 60%, var(--frame) 100%);
  }
  .bag--back .bag__seal { top: 72px; height: 10px; border-color: rgba(80,130,40,.55); }
  .bag--back .brand-name { top: 120px; font-size: 46px; color: var(--paper); }
  .bag--back .tagline { top: 172px; }
  .bag--back .splash { left: 18px; top: 372px; width: 300px; height: 170px; }

  .origin {
    position: absolute; right: 40px; top: 500px;
    font-family: "Barlow Condensed", sans-serif;
    font-weight: 600; font-size: 14px; color: var(--paper);
  }
  .marks { position: absolute; right: 20px; top: 524px; display: flex; gap: 14px; }
  .mark {
    width: 32px; height: 32px; border-radius: 50%;
    background: radial-gradient(circle at 40% 35%, #ffffff, #d6d6d6);
    border: 3px solid #cfd8c2;
  }
</style>
</head>
<body>
  <section class="bag bag--front">
    <div class="bag__panel">
      <div class="bag__seal"></div>
      <svg class="bag__tab" width="388" height="270" viewBox="0 0 388 270" aria-hidden="true">
        <defs>
          <radialGradient id="tabFill" cx="50%" cy="25%" r="70%">
            <stop offset="0" stop-color="#b9d935"/>
            <stop offset="1" stop-color="#6a9f35"/>
          </radialGradient>
        </defs>
        <path d="M71 0 H316 V80 Q316 92 304 92 H213 V264 Q213 276 201 276 H187 Q175 276 175 264 Q175 276 163 276 H149 Q137 276 137 264 H145 V92 H83 Q71 92 71 80 Z" fill="none"/>
        <path d="M71 0 H316 V80 Q316 92 304 92 H256 V176 Q256 192 240 192 H148 Q132 192 132 176 V92 H83 Q71 92 71 80 Z" fill="url(#tabFill)"/>
        <circle cx="194" cy="146" r="22" fill="#ffffff"/>
        <path d="M143 30 H171 Q173 18 183 16 Q193 18 195 30 H218 Q228 30 228 40 Q228 50 218 50 H143 Q133 50 133 40 Q133 30 143 30 Z" fill="#ffffff"/>
      </svg>
      <div class="brand-name">VERALINK</div>
      <div class="tagline">Audio and Video Products</div>
      <div class="splash" role="img" aria-label="Green paint splash and brush stroke"></div>
    </div>
    <div class="slogan-band">For a Pure Connection</div>
  </section>

  <section class="bag bag--back">
    <div class="bag__panel">
      <svg class="hang-hole" style="left:143px;top:14px" width="102" height="28" viewBox="0 0 102 28" aria-hidden="true">
        <path d="M10 8 H44 Q46 0 51 0 Q56 0 58 8 H92 Q102 8 102 18 Q102 28 92 28 H10 Q0 28 0 18 Q0 8 10 8 Z" fill="#ffffff"/>
      </svg>
      <div class="bag__seal"></div>
      <div class="brand-name">VERALINK</div>
      <div class="tagline">Audio and Video Products</div>
      <div class="splash" role="img" aria-label="Green paint splash and brush stroke"></div>
      <div class="origin">MADE IN CHINA</div>
      <div class="marks">
        <span class="mark"></span>
        <span class="mark"></span>
        <span class="mark"></span>
      </div>
    </div>
  </section>
</body>
</html>
```